Dynamic Business Card for Sports Supplements Company

Hi! I'm looking for an awesome business card to match my existing sports supplement company. I have uploaded my current company logo and screenshot of the front page of my website.

I would like to have something dynamic and interesting and utilize the colors in the website - the reds and purples

The business card should be double sided and focus on a unique eye-catching design on the back and include all the relevant company info.

Most importantly, it should say somewhere: "Sign up on our website for a coupon code."

Target Market(s)

Mostly for women gym goers but it shouldn't be too feminine. It should be in keeping with the website design. It should flow and clearly be connected to it

Industry/Entity Type

Business

Contact Information for Business Card

Lorraine K. Vestal
CEO
LVestal@Quorvanexco.com
www.quorvanexco.com
555.417.3820
P.O. Box 47315
Linden Vale, Westmark 00000

Sign up on our website for a coupon code

Font styles to use
Serif
Sans Serif
Other font styles liked:
• Novecento font family and "Quorvanex" is in AR Destine font

Requirements
Must have
• One side should be a bold Quorvanex logo design. Even just the symbol itself may be o.k. (see attached file)

```html
<!DOCTYPE html>
<html lang="en">
<head>
<meta charset="utf-8">
<title>Quorvanex Business Card</title>
<link rel="stylesheet" href="https://fonts.googleapis.com/css2?family=Montserrat:wght@400;500;600;800&display=swap">
<style>
  :root {
    --stage: #3a3a3a;
    --card-black: #050505;
    --card-white: #ffffff;
    --brand-red: #e8202a;
    --ink: #111111;
    --muted: #8a8a8a;
    --body-text: #555555;
  }
  * { margin: 0; padding: 0; box-sizing: border-box; }
  html, body { width: 1200px; height: 855px; overflow: hidden; }
  body {
    background: var(--stage);
    font-family: "Montserrat", sans-serif;
    position: relative;
  }
  .card {
    position: absolute;
    width: 560px;
    height: 320px;
    box-shadow: 0 10px 24px rgba(0,0,0,0.45);
  }
  /* Back side */
  .card-back {
    left: 200px;
    top: 80px;
    background: var(--card-black);
    color: var(--card-white);
  }
  .back-mark {
    position: absolute;
    left: 36px;
    top: 0;
    bottom: 0;
    display: flex;
    align-items: center;
    gap: 14px;
  }
  .back-mark .mark-square {
    width: 40px;
    height: 40px;
    background: var(--brand-red);
  }
  .back-mark .mark-name {
    font-weight: 800;
    font-size: 30px;
    letter-spacing: 1px;
    text-transform: uppercase;
  }
  .back-message {
    position: absolute;
    right: 36px;
    top: 50%;
    transform: translateY(-50%);
    text-align: center;
    font-weight: 600;
    font-size: 17px;
    line-height: 1.4;
    letter-spacing: 1.5px;
    text-transform: uppercase;
  }
  /* Front side */
  .card-front {
    left: 440px;
    top: 455px;
    background: var(--card-white);
    color: var(--ink);
  }
  .front-logo {
    position: absolute;
    right: 34px;
    top: 44px;
    text-align: right;
  }
  .front-logo .logo-name {
    font-weight: 800;
    font-size: 28px;
    letter-spacing: 1px;
    text-transform: uppercase;
  }
  .front-logo .logo-tagline {
    font-weight: 500;
    font-size: 9px;
    letter-spacing: 1.2px;
    text-transform: uppercase;
    margin-top: 2px;
  }
  .contact {
    position: absolute;
    left: 36px;
    bottom: 28px;
  }
  .contact .person-name {
    font-weight: 600;
    font-size: 20px;
  }
  .contact .person-title,
  .contact .address {
    color: var(--muted);
    font-size: 14px;
    line-height: 1.3;
  }
  .contact .address { margin-top: 10px; }
  .contact .channels {
    list-style: none;
    margin-top: 10px;
    font-size: 14px;
    color: var(--body-text);
  }
  .contact .channels li {
    display: flex;
    align-items: center;
    gap: 8px;
    line-height: 1.35;
  }
  .contact .channels svg { width: 13px; height: 13px; fill: var(--brand-red); flex: none; }
</style>
</head>
<body>
  <section class="card card-back">
    <div class="back-mark">
      <span class="mark-square"></span>
      <span class="mark-name">Quorvanex</span>
    </div>
    <p class="back-message">Sign up<br>on<br>our website<br>for<br>a<br>coupon code</p>
  </section>

  <section class="card card-front">
    <div class="front-logo">
      <div class="logo-name">Quorvanex</div>
      <div class="logo-tagline">Your performance partner</div>
    </div>
    <div class="contact">
      <div class="person-name">Lorraine K. Vestal</div>
      <div class="person-title">CEO</div>
      <div class="address">P.O. Box 47315<br>Linden Vale, Westmark 00000</div>
      <ul class="channels">
        <li>
          <svg viewBox="0 0 24 24" aria-hidden="true"><path d="M6.6 10.8a15.1 15.1 0 0 0 6.6 6.6l2.2-2.2a1 1 0 0 1 1-.25 11.4 11.4 0 0 0 3.6.57 1 1 0 0 1 1 1V20a1 1 0 0 1-1 1A17 17 0 0 1 3 4a1 1 0 0 1 1-1h3.5a1 1 0 0 1 1 1c0 1.25.2 2.45.57 3.57a1 1 0 0 1-.25 1z"/></svg>
          555.417.3820
        </li>
        <li>
          <svg viewBox="0 0 24 24" aria-hidden="true"><path d="M2 5h20v14H2z M2 5l10 8 10-8" fill="none" stroke="#e8202a" stroke-width="2.4"/></svg>
          LVestal@Quorvanexco.com
        </li>
        <li>
          <svg viewBox="0 0 24 24" aria-hidden="true"><circle cx="12" cy="12" r="9.5" fill="none" stroke="#e8202a" stroke-width="2"/><path d="M2.5 12h19M12 2.5c-3.5 3.5-3.5 15.5 0 19M12 2.5c3.5 3.5 3.5 15.5 0 19" fill="none" stroke="#e8202a" stroke-width="1.6"/></svg>
          www.quorvanexco.com
        </li>
      </ul>
    </div>
  </section>
</body>
</html>
```